business card

Business card for new business.
Red and black corporate colors.
Card can have an Indsutrial feel to it. Feel free to add Rust, Bolted steel, or graphics as you see fit. We provide highly specialized services to the below mentioned industries.
Keep information out of corners so that if I want I can choose rounded corners.
Information
- front. name - title - phone - email
- Rear
Refining - Rail - Infrastructure - Mining - Energy
Halston - Ashford - North Kingsley - Glenbrook - Westhaven

```html
<!DOCTYPE html>
<html lang="en">
<head>
<meta charset="utf-8">
<title>Ironforge Business Card</title>
<link rel="stylesheet" href="https://fonts.googleapis.com/css2?family=Oswald:wght@600&family=Roboto:wght@400;700;900&display=swap">
<style>
  :root {
    --backdrop: #5b3f2b;
    --card-dark: #1b1b1b;
    --card-mid: #2f2f2f;
    --brand-red: #e3101e;
    --title-grey: #8c8c8c;
    --logo-grey: #8a8a8a;
    --text-white: #f2f2f2;
    --rule: #4a4a4a;
  }
  * { margin: 0; padding: 0; box-sizing: border-box; }
  html, body { width: 1200px; height: 960px; overflow: hidden; }
  body { background: var(--backdrop); position: relative; font-family: 'Roboto', sans-serif; }

  .card {
    position: absolute;
    width: 600px;
    height: 341px;
    background: radial-gradient(ellipse at 50% 35%, var(--card-mid) 0%, var(--card-dark) 80%);
    box-shadow: 0 4px 10px rgba(0,0,0,0.45);
  }
  .card--front { left: 302px; top: 130px; }
  .card--back { left: 299px; top: 489px; }

  .identity {
    position: absolute;
    right: 330px;
    top: 128px;
    text-align: right;
  }
  .identity__name {
    font-family: 'Oswald', sans-serif;
    font-weight: 600;
    font-size: 29px;
    line-height: 34px;
    color: var(--brand-red);
    letter-spacing: 0.2px;
  }
  .identity__title {
    font-weight: 700;
    font-size: 16px;
    line-height: 22px;
    color: var(--title-grey);
  }

  .contacts {
    position: absolute;
    left: 293px;
    top: 125px;
    list-style: none;
  }
  .contacts__item {
    display: flex;
    align-items: center;
    height: 19px;
    font-size: 14.5px;
    color: var(--text-white);
  }
  .contacts__icon { width: 13px; height: 13px; margin-right: 9px; fill: var(--brand-red); }

  .divider {
    position: absolute;
    left: 71px;
    right: 72px;
    top: 231px;
    height: 1px;
    background: var(--rule);
  }

  .services {
    position: absolute;
    left: 0;
    width: 578px;
    top: 252px;
    text-align: center;
    font-weight: 700;
    font-size: 14px;
    line-height: 18px;
    color: var(--brand-red);
  }
  .services .sep { color: var(--title-grey); font-weight: 400; }

  .brand {
    position: absolute;
    left: 0; right: 0;
    top: 143px;
    display: flex;
    justify-content: center;
    align-items: center;
    gap: 14px;
  }
  .brand__mark { width: 22px; height: 22px; background: var(--brand-red); }
  .brand__name {
    font-weight: 900;
    font-size: 50px;
    line-height: 54px;
    color: var(--logo-grey);
    letter-spacing: 0.5px;
  }
</style>
</head>
<body>
  <section class="card card--front">
    <div class="identity">
      <p class="identity__name">MARK ELLISON</p>
      <p class="identity__title">CEO/FOUNDER</p>
    </div>
    <ul class="contacts">
      <li class="contacts__item">
        <svg class="contacts__icon" viewBox="0 0 24 24"><path d="M6.6 10.8a15.1 15.1 0 0 0 6.6 6.6l2.2-2.2a1 1 0 0 1 1-.25 11.4 11.4 0 0 0 3.6.57 1 1 0 0 1 1 1V20a1 1 0 0 1-1 1A17 17 0 0 1 3 4a1 1 0 0 1 1-1h3.5a1 1 0 0 1 1 1c0 1.25.2 2.45.57 3.57a1 1 0 0 1-.25 1z"/></svg>
        555 214 0873
      </li>
      <li class="contacts__item">
        <svg class="contacts__icon" viewBox="0 0 24 24"><path d="M2 5h20v14H2z"/><path d="M3 6l9 7 9-7" fill="none" stroke="#1b1b1b" stroke-width="1.6"/></svg>
        info@ironforge.com
      </li>
      <li class="contacts__item">
        <svg class="contacts__icon" viewBox="0 0 24 24"><circle cx="12" cy="12" r="10"/><path d="M2 12h20M12 2c3 3 3 17 0 20M12 2c-3 3-3 17 0 20" fill="none" stroke="#1b1b1b" stroke-width="1.5"/></svg>
        www.ironforge.com
      </li>
    </ul>
    <div class="divider"></div>
    <p class="services">
      WELDING <span class="sep">|</span> PIPING <span class="sep">|</span> FABRICATION <span class="sep">|</span> RIGGING<br>
      POWER <span class="sep">|</span> HALSTON <span class="sep">|</span> ASHFORD <span class="sep">|</span> NORTH KINGSLEY<br>
      GLENBROOK <span class="sep">|</span> WESTHAVEN
    </p>
  </section>

  <section class="card card--back">
    <div class="brand">
      <span class="brand__mark"></span>
      <span class="brand__name">IRONFORGE</span>
    </div>
  </section>
</body>
</html>
```